Commercial Swimming Pool - Design-Build Contractor Website Design

I need a new website that will feature our newly developed logo and trade name as well as provide a fully updated site experience. We are not a residential builder - we strictly design and install high-end commercial pools. I need the website to highlight our portfolio and communicate the various types of projects in which we specialize. I want the effect of the site to reflect the high-end nature of our services - projects like the 57th floor spa at the Phila Silver Willow, the aquatic therapy portion of the Phila Ravenhawks training facility, a 5om indoor competition pool for the prestigious Dallowmere Academy, the indoor water park at The Quenwick Lodge or the recent country club renovation projects we've completed in our region (to name a few examples).
Need extra days to review

```html
<!DOCTYPE html>
<html lang="en">
<head>
<meta charset="utf-8">
<title>Corwell Aquatics — Commercial Pool Design &amp; Construction</title>
<link href="https://fonts.googleapis.com/css2?family=Josefin+Sans:wght@400;600;700&family=Lato:wght@400;700&display=swap" rel="stylesheet">
<style>
:root{
  --navy:#0f1f45;
  --ink:#111;
  --sky:#3fb6e8;
  --sky-deep:#1d8fd0;
  --pool:#4fc0ea;
  --pale:#e8f4fa;
  --white:#fff;
  --muted:#555;
}
*{box-sizing:border-box;margin:0;padding:0}
html,body{width:1200px;height:3350px;overflow:hidden}
body{position:relative;font-family:'Lato',sans-serif;color:var(--ink);
  background:linear-gradient(180deg,#fff 0,#fff 1080px,#dff0f8 1200px,#a9d8ef 1560px,#d7edf7 1700px,#fff 2300px,#fff 3350px)}
.abs{position:absolute}
.head-font{font-family:'Josefin Sans',sans-serif}
/* header */
.brand{left:112px;top:10px;display:flex;align-items:center;gap:12px}
.brand-mark{width:46px;height:46px;background:var(--navy)}
.brand-name{font-family:'Josefin Sans',sans-serif;font-weight:700;font-size:30px;color:var(--navy);line-height:1}
.brand-sub{font-family:'Lato',sans-serif;font-size:9px;letter-spacing:1px;color:var(--navy);margin-top:4px}
.call{left:741px;top:10px;display:flex;align-items:center;gap:8px;font-family:'Josefin Sans',sans-serif;font-weight:600;font-size:14px}
.call-icon{width:28px;height:28px;border-radius:50%;background:var(--sky);display:flex;align-items:center;justify-content:center}
.btn-contact{left:968px;top:7px;width:120px;height:34px;border-radius:17px;background:var(--sky);color:#fff;font-family:'Josefin Sans',sans-serif;font-weight:600;font-size:14px;display:flex;align-items:center;justify-content:center}
.nav-rule{left:595px;top:50px;width:493px;height:1px;background:#ddd}
.main-nav{left:560px;top:64px;width:530px;display:flex;justify-content:space-between;font-family:'Josefin Sans',sans-serif;font-size:13px;font-weight:600;letter-spacing:.5px}
.main-nav .active{color:var(--sky);text-decoration:underline}
/* hero */
.hero{left:0;top:100px;width:1200px;height:548px;background:linear-gradient(180deg,#45b9ea 0%,#3aa8e0 45%,#2f8fd0 100%)}
.hero-wave{left:0;top:90px;width:1200px;height:50px}
.hero-title{left:0;top:183px;width:1200px;text-align:center;font-family:'Josefin Sans',sans-serif;font-weight:700;font-size:44px;color:#fff;text-shadow:0 3px 6px rgba(0,40,90,.45)}
.hero-tags{left:0;top:252px;width:1200px;text-align:center;font-family:'Josefin Sans',sans-serif;font-weight:600;font-size:19px;color:#fff;letter-spacing:1px;word-spacing:4px}
.hero-tags span{margin:0 22px}
.btn-light{background:#fff;color:var(--navy);font-family:'Josefin Sans',sans-serif;font-weight:600;border-radius:24px;display:flex;align-items:center;justify-content:center;box-shadow:3px 4px 0 rgba(0,0,0,.12)}
.hero-btn{left:519px;top:293px;width:162px;height:46px;font-size:16px}
/* section titles */
.section-title{left:0;width:1200px;text-align:center;font-family:'Josefin Sans',sans-serif;font-weight:700;font-size:37px;letter-spacing:1.5px;color:var(--ink)}
/* project cards */
.card{width:306px;height:381px;top:756px;background:#fff;border-radius:14px;box-shadow:0 4px 18px rgba(0,60,110,.12)}
.card-photo{position:absolute;left:15px;top:18px;width:276px;height:302px;border-radius:12px}
.card-caption{position:absolute;left:30px;top:284px;width:246px;height:88px;background:#fff;border-radius:16px 16px 0 0;text-align:center;font-family:'Josefin Sans',sans-serif;font-size:15px;line-height:25px;padding-top:10px}
.arrow{width:20px;height:20px;border-radius:50%;background:#111;top:928px;display:flex;align-items:center;justify-content:center}
/* about */
.about-mark{left:112px;top:1265px;width:420px;height:310px;display:flex;align-items:center;gap:18px}
.about-mark .sq{width:54px;height:54px;background:var(--navy)}
.about-mark .name{font-family:'Josefin Sans',sans-serif;font-weight:700;font-size:50px;line-height:1.05;color:var(--navy)}
.about-title{left:561px;top:1262px;font-family:'Josefin Sans',sans-serif;font-weight:700;font-size:35px;letter-spacing:1px}
.about-text{left:561px;top:1310px;width:530px;font-size:14.5px;line-height:25.8px;color:#222}
.about-text p+p{margin-top:25px}
.about-btn{left:561px;top:1558px;width:162px;height:46px;font-size:16px}
/* portfolio */
.tile{border-radius:10px}
/* splash */
.splash{left:0;top:2315px;width:1200px;height:250px;background:linear-gradient(180deg,rgba(255,255,255,0) 0%,#8ecbea 30%,#3c94c9 50%,#b5dbef 75%,rgba(255,255,255,0) 100%)}
/* contact */
.field{left:112px;width:332px;height:50px;background:#fff;box-shadow:0 3px 10px rgba(0,0,0,.12);font-size:14px;color:#444;padding:18px 17px}
.message{left:465px;top:2650px;width:314px;height:240px;background:#fff;box-shadow:0 3px 10px rgba(0,0,0,.12);font-size:14px;color:#444;padding:18px 17px}
.submit{left:114px;top:2840px;width:332px;height:50px;background:var(--sky);color:#fff;font-weight:700;font-size:17px;display:flex;align-items:center;justify-content:center;box-shadow:0 3px 6px rgba(0,0,0,.15)}
.info{left:815px;display:flex;gap:14px}
.info-icon{width:62px;height:62px;border-radius:50%;background:var(--sky);display:flex;align-items:center;justify-content:center;box-shadow:0 4px 8px rgba(0,80,140,.25);flex:none}
.info h4{font-family:'Josefin Sans',sans-serif;font-weight:600;font-size:18px;letter-spacing:1px;margin-top:4px}
.info p{font-size:14.5px;line-height:27px;color:#333}
/* footer */
.footer{left:0;top:2915px;width:1200px;height:435px;background:linear-gradient(180deg,rgba(255,255,255,0) 0%,#6cbfe8 12%,#1f8ed6 30%,#2a9be0 60%,#5ab8ec 100%)}
.foot-brand{left:0;top:3075px;width:1200px;display:flex;justify-content:center;align-items:center;gap:14px}
.foot-brand .sq{width:56px;height:56px;background:var(--navy)}
.foot-brand .name{font-family:'Josefin Sans',sans-serif;font-weight:700;font-size:40px;color:var(--navy);line-height:1}
.foot-nav{left:260px;top:3180px;width:680px;display:flex;justify-content:space-between;font-family:'Josefin Sans',sans-serif;font-weight:700;font-size:13px;color:var(--navy)}
.social{top:3222px;width:30px;height:30px;border-radius:50%;background:#111}
.copyright{left:0;top:3277px;width:1200px;text-align:center;font-family:'Josefin Sans',sans-serif;font-weight:600;font-size:12px;color:var(--navy)}
</style>
</head>
<body>

<header>
  <div class="abs brand"><div class="brand-mark"></div><div><div class="brand-name">CORWELL<br>AQUATICS</div><div class="brand-sub">DESIGN | CONSTRUCTION | EXCELLENCE</div></div></div>
  <div class="abs call"><span class="call-icon"><svg width="14" height="14" viewBox="0 0 24 24"><path fill="#fff" d="M6.6 10.8a15 15 0 0 0 6.6 6.6l2.2-2.2c.3-.3.7-.4 1-.2 1.1.4 2.3.6 3.6.6.6 0 1 .4 1 1V20c0 .6-.4 1-1 1A17 17 0 0 1 3 4c0-.6.4-1 1-1h3.5c.6 0 1 .4 1 1 0 1.3.2 2.5.6 3.6.1.3 0 .7-.2 1z"/></svg></span>CALL US: +1 555 014 2290</div>
  <div class="abs btn-contact">CONTACT US</div>
  <div class="abs nav-rule"></div>
  <nav class="abs main-nav"><span class="active">HOME</span><span>ABOUT US</span><span>PROJECT</span><span>PORTFOLIO</span><span>REVIEWS</span></nav>
</header>

<section>
  <div class="abs hero" role="img" aria-label="Underwater photo of children swimming in a blue pool"></div>
  <svg class="abs hero-wave" viewBox="0 0 1200 50" preserveAspectRatio="none"><path fill="#fff" d="M0 0H1200V18C1000 40 820 10 600 40 380 10 200 38 0 14Z"/><path fill="none" stroke="#1d5fa8" stroke-width="3" d="M0 14C200 38 380 10 600 40 820 10 1000 40 1200 18"/></svg>
  <h1 class="abs hero-title">WELCOME TO CORWELL AQUATICS</h1>
  <div class="abs hero-tags"><span>DESIGN</span>|<span>CONSTRUCTION</span>|<span>EXCELLANCE</span></div>
  <div class="abs btn-light hero-btn">GET STARTED</div>
</section>

<section>
  <h2 class="abs section-title" style="top:690px">OUR PROJECT</h2>
  <div class="abs arrow" style="left:40px"><svg width="10" height="10" viewBox="0 0 10 10"><path d="M7 1 3 5l4 4" stroke="#fff" stroke-width="2" fill="none"/></svg></div>
  <div class="abs arrow" style="left:1137px"><svg width="10" height="10" viewBox="0 0 10 10"><path d="M3 1l4 4-4 4" stroke="#fff" stroke-width="2" fill="none"/></svg></div>
  <div class="abs card" style="left:112px"><div class="card-photo" role="img" aria-label="Rooftop spa with fountain and palm trees" style="background:linear-gradient(180deg,#bcdcf2,#7fb36a 45%,#2a7fd0 80%,#1e6fc4)"></div><div class="card-caption">57th floor spa<br>at the Phila Silver Willow</div></div>
  <div class="abs card" style="left:447px"><div class="card-photo" role="img" aria-label="Therapy pool with palm trees" style="background:linear-gradient(180deg,#3f7fcf,#8cb6e0 30%,#3d6a45 45%,#3cc4d4 60%,#1e9fb5)"></div><div class="card-caption">The aquatic therapy portion<br>of the Phila Ravenhawks training facility</div></div>
  <div class="abs card" style="left:782px"><div class="card-photo" role="img" aria-label="Competition pool with ladder under bright sky" style="background:linear-gradient(180deg,#2f6fc0,#a8d3f2 40%,#6fc4ea 60%,#2e95d8)"></div><div class="card-caption">5om indoor competition pool<br>for the prestigious Dallowmere Academy</div></div>
</section>

<section>
  <div class="abs about-mark"><div class="sq"></div><div class="name">CORWELL<br>AQUATICS</div></div>
  <h2 class="abs about-title">ABOUT CORWELL AQUATICS</h2>
  <div class="abs about-text">
    <p>Nam libero tempore, cum soluta nobis est eligendi optio cumque nihil impedit quo minus id quod maxime placeat facere possimus, omnis voluptas assumenda est, omnis dolor repellendus. Temporibus autem quibusdam et aut officiis debitis aut rerum necessitatibus saepe eveniet ut et voluptates repudiandae sint et molestiae non recusandae.</p>
    <p>Itaque earum rerum hic tenetur a sapiente delectus, ut aut reiciendis voluptatibus maiores alias consequatur aut perferendis doloribus asperiores repellat.</p>
  </div>
  <div class="abs btn-light about-btn">READ MORE</div>
</section>

<section>
  <h2 class="abs section-title" style="top:1703px">PORTFOLIO</h2>
  <div class="abs tile" role="img" aria-label="Outdoor pool surrounded by trees" style="left:110px;top:1790px;width:283px;height:332px;background:linear-gradient(180deg,#5f8cc4,#2f5a2e 40%,#3fd0dc 65%,#7a6a5e)"></div>
  <div class="abs tile" role="img" aria-label="Pool at dusk with lit water" style="left:110px;top:2134px;width:283px;height:151px;background:linear-gradient(180deg,#1d3f86,#2a4878 50%,#7fd4ee 75%,#3a3a46)"></div>
  <div class="abs tile" role="img" aria-label="Children swimming underwater" style="left:408px;top:1790px;width:380px;height:495px;background:linear-gradient(180deg,#5fb0ea,#2e8ad6 60%,#1c6fc0)"></div>
  <div class="abs tile" role="img" aria-label="Resort pool with palm trees" style="left:804px;top:1790px;width:284px;height:152px;background:linear-gradient(180deg,#7fa4d8,#3d6a45 35%,#35b8cc 60%,#1e8fae)"></div>
  <div class="abs tile" role="img" aria-label="Spa fountain with palm trees" style="left:804px;top:1953px;width:284px;height:332px;background:linear-gradient(180deg,#2d6fd0,#bfd9ef 35%,#7fb36a 55%,#2a7fd0 80%,#1e6fc4)"></div>
</section>

<div class="abs splash" role="img" aria-label="Water splash with bubbles"></div>

<section>
  <h2 class="abs section-title" style="top:2578px">GET IN TOUCH WITH US</h2>
  <div class="abs field" style="top:2650px">Name</div>
  <div class="abs field" style="top:2713px">Your Phone</div>
  <div class="abs field" style="top:2775px">Your Email</div>
  <div class="abs submit">SUBMIT</div>
  <div class="abs message">Message</div>
  <div class="abs info" style="top:2650px"><span class="info-icon"><svg width="20" height="24" viewBox="0 0 20 24"><path fill="#fff" d="M10 0a8 8 0 0 0-8 8c0 6 8 16 8 16s8-10 8-16a8 8 0 0 0-8-8zm0 11a3 3 0 1 1 0-6 3 3 0 0 1 0 6z"/></svg></span><div><h4>LOCATION</h4><p>Corwell Aquatics<br>United States</p></div></div>
  <div class="abs info" style="top:2755px"><span class="info-icon"><svg width="22" height="22" viewBox="0 0 24 24"><path fill="#fff" d="M6.6 10.8a15 15 0 0 0 6.6 6.6l2.2-2.2c.3-.3.7-.4 1-.2 1.1.4 2.3.6 3.6.6.6 0 1 .4 1 1V20c0 .6-.4 1-1 1A17 17 0 0 1 3 4c0-.6.4-1 1-1h3.5c.6 0 1 .4 1 1 0 1.3.2 2.5.6 3.6.1.3 0 .7-.2 1z"/></svg></span><div><h4>PHONE NUMBER</h4><p>+1 555 014 2290</p></div></div>
  <div class="abs info" style="top:2835px"><span class="info-icon"><svg width="22" height="16" viewBox="0 0 22 16"><rect width="22" height="16" rx="2" fill="#fff"/><path d="M1 2l10 7 10-7" stroke="#3fb6e8" stroke-width="2" fill="none"/></svg></span><div><h4>EMAIL ADDRESS</h4><p>info@corwellaquatics.com</p></div></div>
</section>

<footer>
  <div class="abs footer" role="img" aria-label="Underwater view with surface waves"></div>
  <div class="abs foot-brand"><div class="sq"></div><div class="name">CORWELL AQUATICS</div></div>
  <nav class="abs foot-nav"><span>HOME</span><span>ABOUT US</span><span>PROJECT</span><span>PORTFOLIO</span><span>REVIEWS</span><span>CONTACT US</span></nav>
  <div class="abs social" style="left:538px"></div>
  <div class="abs social" style="left:587px"></div>
  <div class="abs social" style="left:632px"></div>
  <div class="abs copyright">Copyrights@2023 Corwell Aquatics.All Rights Reserved</div>
</footer>

</body>
</html>
```